Create a memorable Stationary for Security Software Company

Velbrantix is the worldwide leader in securing the Internet. Making Internet communications and critical data secure, reliable and available everywhere has been and continues to be our ongoing vision. We are committed to staying focused on real customer needs and to developing new and innovative security solutions that redefine the security landscape.

Industry/Entity Type

Internet

Font styles to use
Serif
Sans Serif
Script

Colors
0792cd
33a6d7
85cae6

```html
<!DOCTYPE html>
<html lang="en">
<head>
<meta charset="utf-8">
<title>Velbrantix Business Card</title>
<link rel="stylesheet" href="https://fonts.googleapis.com/css2?family=Source+Sans+3:wght@400;600;700&display=swap">
<style>
  :root {
    --brand-deep: #0792cd;
    --brand-mid: #33a6d7;
    --brand-light: #85cae6;
    --ink: #2a3a45;
    --paper: #ffffff;
    --stage: #ecebe8;
    --edge: #4a4a4a;
  }
  * { margin: 0; padding: 0; box-sizing: border-box; }
  html, body { width: 1200px; height: 1118px; overflow: hidden; }
  body {
    background: var(--stage);
    font-family: "Source Sans 3", "Myriad Pro", sans-serif;
    position: relative;
  }
  .card {
    position: absolute;
    width: 818px;
    height: 468px;
    border-radius: 40px;
    overflow: hidden;
    border: 1.5px solid var(--edge);
  }
  .card-front { left: 336px; top: 63px; background: var(--brand-light); }
  .card-back { left: 60px; top: 607px; background: var(--paper); }

  .wave-band { position: absolute; inset: 0; width: 100%; height: 100%; }

  .brand-lockup {
    position: absolute;
    display: flex;
    align-items: center;
    gap: 14px;
    color: var(--brand-mid);
    font-weight: 700;
    font-size: 50px;
    letter-spacing: 0.5px;
  }
  .brand-dot {
    width: 34px; height: 34px; border-radius: 50%;
    background: var(--brand-mid);
  }
  .card-front .brand-lockup { left: 96px; top: 172px; }
  .card-back .brand-lockup { left: 236px; top: 160px; font-size: 56px; }

  .contact-divider {
    position: absolute; left: 447px; top: 111px;
    width: 1px; height: 137px; background: #6a9db5;
  }
  .contact-list { position: absolute; left: 466px; top: 110px; list-style: none; }
  .contact-list li {
    display: flex; align-items: center; gap: 10px;
    height: 37px; font-size: 21px; color: var(--ink);
  }
  .contact-list svg { width: 18px; height: 18px; fill: #3c5564; }

  .holder { position: absolute; right: 64px; top: 352px; text-align: right; color: var(--paper); }
  .holder-name { font-size: 32px; font-weight: 700; line-height: 1.1; }
  .holder-title { font-size: 27px; font-weight: 400; letter-spacing: 1px; line-height: 1.3; }

  .address {
    position: absolute; left: 50px; top: 398px;
    display: flex; gap: 10px; color: var(--paper); font-size: 20px; line-height: 28px;
  }
  .address svg { width: 18px; height: 20px; fill: var(--paper); margin-top: 4px; }

  .back-url {
    position: absolute; left: 0; right: 0; top: 358px; text-align: center;
    font-size: 25px; letter-spacing: 6px; color: #222;
  }
</style>
</head>
<body>

<section class="card card-front" aria-label="Business card front">
  <svg class="wave-band" viewBox="0 0 818 468" preserveAspectRatio="none" aria-hidden="true">
    <path d="M0,262 C170,350 360,392 540,355 C660,330 740,305 818,300 L818,468 L0,468 Z" fill="var(--brand-mid)"/>
    <path d="M0,285 C170,370 360,405 540,368 C660,345 740,318 818,314 L818,468 L0,468 Z" fill="var(--brand-deep)"/>
    <path d="M0,270 C170,358 360,398 540,362 C660,337 740,311 818,307" fill="none" stroke="#ffffff" stroke-width="2.5" opacity="0.85"/>
    <path d="M0,298 C170,380 360,412 540,376 C660,352 740,326 818,321" fill="none" stroke="#ffffff" stroke-width="1.5" opacity="0.6"/>
  </svg>

  <div class="brand-lockup"><span class="brand-dot"></span>Velbrantix</div>

  <div class="contact-divider"></div>
  <ul class="contact-list">
    <li><svg viewBox="0 0 20 20"><path d="M5 2l3 4-2 2c1 2.5 3 4.5 5.5 5.5l2-2 4 3-2 3.5C9 17 3 11 1.5 4z"/></svg>012-345-6789</li>
    <li><svg viewBox="0 0 20 20"><path d="M6 1h8a1 1 0 011 1v16a1 1 0 01-1 1H6a1 1 0 01-1-1V2a1 1 0 011-1zm1 2v11h6V3zm3 13a1 1 0 100 2 1 1 0 000-2z"/></svg>012-345-6789</li>
    <li><svg viewBox="0 0 20 20"><path d="M2 5h16v11H2zM3 6l7 5 7-5v-.5H3z"/></svg>info@velbrantix.com.com</li>
    <li><svg viewBox="0 0 20 20"><path d="M10 1a9 9 0 100 18 9 9 0 000-18zm0 2c1.2 1.4 2 3.6 2.2 6H7.8C8 6.6 8.8 4.4 10 3zM3.1 11h2.7c.1 2 .6 3.8 1.4 5.1A7 7 0 013.1 11zm0-2a7 7 0 014.1-5.1C6.4 5.2 5.9 7 5.8 9zm6.9 8c-1.2-1.4-2-3.6-2.2-6h4.4c-.2 2.4-1 4.6-2.2 6zm2.8-.9c.8-1.3 1.3-3.1 1.4-5.1h2.7a7 7 0 01-4.1 5.1zM14.2 9c-.1-2-.6-3.8-1.4-5.1A7 7 0 0116.9 9z"/></svg>www.velbrantix.com.com</li>
  </ul>

  <div class="address">
    <svg viewBox="0 0 18 20"><path d="M9 0a7 7 0 017 7c0 5-7 13-7 13S2 12 2 7a7 7 0 017-7zm0 4a3 3 0 100 6 3 3 0 000-6z"/></svg>
    <div>Street Name, City Name<br>Zipcode-012345</div>
  </div>

  <div class="holder">
    <div class="holder-name">Your Name</div>
    <div class="holder-title">Title</div>
  </div>
</section>

<section class="card card-back" aria-label="Business card back">
  <div class="brand-lockup"><span class="brand-dot"></span>Velbrantix</div>
  <div class="back-url">www.velbrantix.com.com</div>
</section>

</body>
</html>
```